Business Cards for new orthopaedic surgery practice

My husband and I are starting our own orthopaedic surgery practice. We are looking for a business card that is uniform, but one will have my name/title and the other will have his. You can just create one design with my name on it for now. But when I choose your design as the winning design I will ask that you add another copy with his name/title.

We are looking for classy, simple, elite all in one. We like dark blues/a little gold/yellow. Something that goes with our logo. We want our logo incorporated. Here is all the info you need:
Business name: RV Bone & Vitality Center
Location: 38517 North Willowmere Ave
Maple Cove, FL 33999
Phone: 954-218-4063
Fax: 954-582-7341
Email: info@myrvbonecare.example

Names: Lydia Vance, M.D.
Board Certified Hand and Upper Extremity Surgeon

Ebo Dansu, M.D.
Board Certified Hip & Knee Replacement/General Orthopaedic Surgeon

Can decide what you want to put on the back. Maybe a slogan:
Steady Hands. Strong Recovery.

I am just going to upload our logo. The only thing is if we select you as the winning design, the location, and phone numbers may change. We will need your help to update that once fully solidified.

Industry/Entity Type

Medical

Contact Information for Business Card

Colors
0054AA
0677BA
7BADD7
CADEEF
E8F1F8
0094D4
00A9DD
6FCCEA
C7EBF8
E9F6FB

Requirements
Must have
• class, appeal,
Should not have
• We want to air on the side of masculine if we are looking at masculine vs. feminine feel. But we still want it classy, sophisticated, and something we will love

```html
<!DOCTYPE html>
<html lang="en">
<head>
<meta charset="utf-8">
<title>RV Bone &amp; Vitality Center – Business Card</title>
<link href="https://fonts.googleapis.com/css2?family=Poppins:wght@400;500;600&display=swap" rel="stylesheet">
<style>
  :root {
    --backdrop: #1c1c1f;
    --card-navy: #253c85;
    --accent-cyan: #15b8e0;
    --accent-deep: #1a6fb8;
    --ink-white: #ffffff;
    --faint-navy: #34509a;
  }
  * { box-sizing: border-box; margin: 0; padding: 0; }
  html, body { width: 1200px; height: 900px; overflow: hidden; }
  body {
    background: var(--backdrop);
    font-family: "Poppins", sans-serif;
    color: var(--ink-white);
    position: relative;
  }
  .card {
    position: absolute;
    left: 280px;
    width: 640px;
    height: 366px;
    background: var(--card-navy);
    overflow: hidden;
    box-shadow: 0 10px 30px rgba(0,0,0,.5);
  }
  .card--front { top: 68px; }
  .card--back { top: 466px; }

  .brand {
    position: absolute;
    display: flex;
    align-items: center;
    gap: 14px;
  }
  .brand__dot {
    width: 34px; height: 34px;
    border-radius: 50%;
    background: var(--ink-white);
    flex: none;
  }
  .brand__name {
    font-weight: 500;
    font-size: 22px;
    line-height: 1.2;
    color: var(--ink-white);
    text-transform: uppercase;
    letter-spacing: 1px;
  }

  .card--front .brand { left: 44px; top: 40px; }
  .card--front .brand__name { width: 250px; }

  .faint-mark {
    position: absolute;
    right: -40px; bottom: -60px;
    width: 300px; height: 300px;
    border-radius: 50%;
    background: var(--faint-navy);
  }

  .person { position: absolute; left: 44px; top: 150px; }
  .person__name { color: var(--accent-cyan); font-weight: 600; font-size: 19px; }
  .person__title { font-size: 13px; margin-top: 2px; }

  .contacts {
    position: absolute; left: 44px; top: 218px;
    font-size: 13px; line-height: 1.75;
  }
  .contacts__row { display: flex; align-items: center; gap: 8px; }
  .contacts__pair { display: flex; gap: 28px; }
  .contacts svg { width: 13px; height: 13px; fill: var(--ink-white); flex: none; }
  .contacts .icon-cyan { fill: var(--accent-cyan); }
  .rule {
    position: absolute; left: 44px; top: 300px;
    width: 440px; height: 1px; background: var(--ink-white);
  }
  .base-band {
    position: absolute; left: 0; right: 0; bottom: 0; height: 22px;
    background: var(--accent-cyan);
  }
  .base-band__tab {
    position: absolute; left: 0; bottom: 22px;
    width: 60px; height: 10px; background: var(--ink-white);
  }

  .card--back .brand { left: 50%; top: 110px; transform: translateX(-50%); }
  .card--back .brand__name { font-size: 26px; width: 300px; }
  .slogan-band {
    position: absolute; left: 0; right: 0; top: 262px; height: 40px;
    background: linear-gradient(90deg, transparent 0%, var(--accent-deep) 25%, var(--accent-cyan) 55%, var(--accent-deep) 80%, transparent 100%);
    display: flex; align-items: center; justify-content: center;
    font-size: 15px; letter-spacing: .3px;
  }
</style>
</head>
<body>
  <section class="card card--front">
    <div class="faint-mark"></div>
    <div class="brand">
      <span class="brand__dot"></span>
      <span class="brand__name">RV Bone &amp; Vitality Center</span>
    </div>
    <div class="person">
      <p class="person__name">Lydia Vance, M.D.</p>
      <p class="person__title">Hand and Upper Extremity Surgery</p>
    </div>
    <div class="contacts">
      <div class="contacts__row">
        <svg viewBox="0 0 24 24"><path d="M6.6 10.8a15 15 0 0 0 6.6 6.6l2.2-2.2c.3-.3.7-.4 1-.2 1.1.4 2.3.6 3.6.6.6 0 1 .4 1 1V20c0 .6-.4 1-1 1A17 17 0 0 1 3 4c0-.6.4-1 1-1h3.5c.6 0 1 .4 1 1 0 1.3.2 2.5.6 3.6.1.3 0 .7-.2 1z"/></svg>
        <span>954-218-4063</span>
      </div>
      <div class="contacts__pair">
        <div class="contacts__row">
          <svg viewBox="0 0 24 24"><path d="M6 2h10v5H6zM4 8h16a2 2 0 0 1 2 2v8h-4v4H6v-4H2v-8a2 2 0 0 1 2-2zm4 8v4h8v-4z"/></svg>
          <span>954-582-7341</span>
        </div>
        <div class="contacts__row">
          <svg class="icon-cyan" viewBox="0 0 24 24"><path d="M2 5h20v14H2zm2 2v.5l8 5 8-5V7z"/></svg>
          <span>info@myrvbonecare.example</span>
        </div>
      </div>
      <div class="contacts__row">
        <span>38517 North Willowmere Ave, Maple Cove, FL 33999</span>
      </div>
    </div>
    <div class="rule"></div>
    <div class="base-band__tab"></div>
    <div class="base-band"></div>
  </section>

  <section class="card card--back">
    <div class="brand">
      <span class="brand__dot"></span>
      <span class="brand__name">RV Bone &amp; Vitality Center</span>
    </div>
    <div class="slogan-band">Steady Hands. Strong Recovery.</div>
  </section>
</body>
</html>
```